Local Roofing/Construction company business needs new biz card design

We need a new business card design, current cards are from the start of this operation and generic at best. We are a local Construction Company (General Contractor) with a majority of our work originating from insurance claims-exterior finish work is the main focus (Roofs-Siding-Gutters etc). Heavily involved with homeowners and the low ball offers they receive from insurance company's after a insurable event takes place. I have attached some of our original logo file(s) below.

```html
<!DOCTYPE html>
<html lang="en">
<head>
<meta charset="utf-8">
<title>Stonefield Builders – Business Card</title>
<link href="https://fonts.googleapis.com/css2?family=Lato:wght@400;700;900&display=swap" rel="stylesheet">
<style>
  :root {
    --backdrop: #2a2c2f;
    --card: #0e1e22;
    --card-edge: #15292e;
    --green: #22d670;
    --white: #f2f4f3;
    --muted: #c9d1cf;
  }
  * { box-sizing: border-box; margin: 0; padding: 0; }
  html, body {
    width: 1200px; height: 952px; overflow: hidden;
    background: var(--backdrop);
    font-family: "Lato", sans-serif;
  }
  .canvas { position: relative; width: 1200px; height: 952px; }
  .card {
    position: absolute;
    width: 520px; height: 300px;
    background: var(--card);
    border-radius: 18px;
    box-shadow: 0 0 0 1px var(--card-edge), 0 18px 40px rgba(0,0,0,.45);
    overflow: hidden;
  }
  .card--front { left: 60px; top: 500px; }
  .card--back { left: 620px; top: 150px; }

  /* brand */
  .brand {
    position: absolute; inset: 0;
    display: flex; align-items: center; justify-content: center; gap: 16px;
  }
  .brand__mark { width: 30px; height: 30px; background: var(--green); }
  .brand__name {
    color: var(--green); font-weight: 900; font-size: 34px;
    letter-spacing: 2px; text-transform: uppercase; line-height: 1;
  }
  .brand--small { inset: auto; left: 150px; top: 34px; gap: 10px; }
  .brand--small .brand__mark { width: 18px; height: 18px; }
  .brand--small .brand__name { font-size: 20px; letter-spacing: 1.5px; }

  /* contact */
  .contact-band { position: absolute; left: 0; top: 112px; width: 240px; height: 166px; }
  .contact-item {
    display: flex; align-items: flex-start; gap: 9px;
    font-size: 12px; line-height: 1.3;
  }
  .contact-address {
    position: absolute; left: 22px; top: 66px;
    color: var(--white);
  }
  .contact-list {
    position: absolute; left: 22px; top: 134px;
    list-style: none; display: flex; flex-direction: column; gap: 10px;
    color: var(--card); font-weight: 700;
  }
  .contact-icon {
    flex: none; width: 15px; height: 15px; border-radius: 3px;
    background: var(--card); display: flex; align-items: center; justify-content: center;
  }
  .contact-address .contact-icon { background: var(--green); }

  /* person */
  .person { position: absolute; right: 34px; top: 150px; text-align: right; }
  .person__name { font-size: 19px; letter-spacing: 1px; color: var(--white); font-weight: 400; }
  .person__name strong { color: var(--green); font-weight: 900; }
  .person__title { margin-top: 4px; font-size: 14px; color: var(--muted); }
</style>
</head>
<body>
<main class="canvas">

  <section class="card card--front" aria-label="Business card front">
    <div class="brand">
      <span class="brand__mark"></span>
      <span class="brand__name">Stonefield Builders</span>
    </div>
  </section>

  <section class="card card--back" aria-label="Business card back">
    <div class="brand brand--small">
      <span class="brand__mark"></span>
      <span class="brand__name">Stonefield Builders</span>
    </div>

    <p class="contact-item contact-address">
      <span class="contact-icon">
        <svg width="9" height="11" viewBox="0 0 9 11"><path d="M4.5 0A4.3 4.3 0 0 0 .2 4.3C.2 7.5 4.5 11 4.5 11s4.3-3.5 4.3-6.7A4.3 4.3 0 0 0 4.5 0zm0 6a1.7 1.7 0 1 1 0-3.4 1.7 1.7 0 0 1 0 3.4z" fill="#0e1e22"/></svg>
      </span>
      <span>2150 Cedar Ridge Avenue<br>Springfield, IL 62704</span>
    </p>

    <svg class="contact-band" viewBox="0 0 240 166" aria-hidden="true">
      <polygon points="0,0 240,0 240,146 222,146 205,166 0,166" fill="#22d670"/>
    </svg>

    <ul class="contact-list">
      <li class="contact-item">
        <span class="contact-icon">
          <svg width="10" height="10" viewBox="0 0 10 10"><path d="M2 0l2 2.5-1.2 1.2a6 6 0 0 0 3.5 3.5L7.5 6 10 8l-1.5 2A8.5 8.5 0 0 1 0 1.5z" fill="#f2f4f3"/></svg>
        </span>
        <span>+00 987 654 32</span>
      </li>
      <li class="contact-item">
        <span class="contact-icon">
          <svg width="11" height="8" viewBox="0 0 11 8"><rect x=".5" y=".5" width="10" height="7" fill="none" stroke="#f2f4f3"/><path d="M.5.5l5 4 5-4" fill="none" stroke="#f2f4f3"/></svg>
        </span>
        <span>office@stonefieldbuild.com</span>
      </li>
      <li class="contact-item">
        <span class="contact-icon">
          <svg width="9" height="10" viewBox="0 0 9 10"><path d="M0 0l9 4-4 1.2L3.5 10z" fill="#f2f4f3"/></svg>
        </span>
        <span>www.stonefieldbuild.com</span>
      </li>
    </ul>

    <div class="person">
      <p class="person__name">DANIEL M. <strong>HARLOW</strong></p>
      <p class="person__title">General Contractor</p>
    </div>
  </section>

</main>
</body>
</html>
```